Dalvick's Business Card

I need some designs for a new business card including the new logo attached. An old example of our business card is also attached to show all the data that should be included on the new design.
**I added some more examples someone had mocked up**

Contact Information for Business Card

Should include all info on other examples uploaded.

```html
<!DOCTYPE html>
<html lang="en">
<head>
<meta charset="UTF-8">
<title>Dalvick's Business Card</title>
<link href="https://fonts.googleapis.com/css2?family=Montserrat:wght@400;500;600;700&display=swap" rel="stylesheet">
<style>
  :root {
    --brand-blue: #1570bb;
    --brand-red: #e3222a;
    --ink: #2b2b2b;
    --card: #ffffff;
    --stage: #e9e7e3;
  }
  * { margin: 0; padding: 0; box-sizing: border-box; }
  html, body { width: 900px; height: 1200px; overflow: hidden; }
  body {
    background: var(--stage);
    font-family: "Montserrat", Arial, sans-serif;
    position: relative;
  }
  .card {
    position: absolute;
    left: 80px;
    width: 742px;
    height: 442px;
    background: var(--card);
    border-radius: 30px;
    overflow: hidden;
    box-shadow: 0 6px 14px rgba(0,0,0,0.25);
  }
  .card--front { top: 131px; }
  .card--back { top: 638px; }

  .brand-mark {
    position: absolute;
    border-radius: 50%;
    background: var(--brand-blue);
  }
  .brand-name {
    position: absolute;
    color: var(--brand-blue);
    font-weight: 700;
    letter-spacing: 0.5px;
    line-height: 1;
    white-space: nowrap;
  }
  .brand-service {
    position: absolute;
    color: var(--brand-red);
    font-weight: 600;
    white-space: nowrap;
    line-height: 1;
  }

  /* Front */
  .card--front .brand-mark { left: 188px; top: 122px; width: 46px; height: 46px; }
  .card--front .brand-name { left: 70px; width: 283px; text-align: center; top: 228px; font-size: 44px; }
  .card--front .brand-service { left: 70px; width: 283px; text-align: center; top: 275px; font-size: 12.5px; }

  .divider {
    position: absolute;
    left: 393px; top: 180px;
    width: 2px; height: 105px;
    background: var(--brand-blue);
  }
  .contact { position: absolute; left: 426px; top: 190px; }
  .contact__name {
    color: var(--brand-blue);
    font-weight: 700;
    font-size: 26px;
    margin-bottom: 20px;
  }
  .contact__line {
    display: flex; align-items: center;
    font-size: 17px; color: var(--ink);
    height: 24px;
  }
  .contact__line svg { width: 15px; height: 15px; margin-right: 12px; flex: none; }

  .ribbon { position: absolute; left: 0; bottom: 0; width: 742px; height: 42px; }
  .ribbon__label {
    position: absolute; bottom: 0; height: 42px;
    display: flex; align-items: center; justify-content: center;
    color: #fff; font-size: 15.5px; font-weight: 500; letter-spacing: 0.3px;
  }
  .ribbon__label--family { left: 0; width: 400px; }
  .ribbon__label--licensed { left: 400px; width: 310px; }

  /* Back */
  .card--back .brand-mark { left: 130px; top: 175px; width: 90px; height: 90px; }
  .card--back .brand-name { left: 246px; top: 186px; font-size: 62px; }
  .card--back .brand-service { left: 248px; top: 249px; font-size: 17px; }
  .footer-band {
    position: absolute; left: 0; bottom: 0;
    width: 100%; height: 17px; background: var(--brand-blue);
  }
</style>
</head>
<body>

<section class="card card--front">
  <div class="brand-mark"></div>
  <div class="brand-name">DALVICK'S</div>
  <div class="brand-service">AIR CONDITIONING &amp; HEATING SERVICE</div>

  <div class="divider"></div>

  <div class="contact">
    <div class="contact__name">Mark Dalvick</div>
    <div class="contact__line">
      <svg viewBox="0 0 16 16" aria-hidden="true">
        <path fill="var(--brand-red)" d="M1 5c0-2 3-3 7-3s7 1 7 3v1.5h-3.5V5h-7v1.5H1z M4 7h8l2 6H2z"/>
        <circle cx="8" cy="10" r="1.6" fill="#fff"/>
      </svg>
      555.014.2290
    </div>
    <div class="contact__line">
      <svg viewBox="0 0 16 16" aria-hidden="true">
        <rect x="1" y="3.5" width="14" height="9.5" fill="var(--brand-blue)"/>
        <path d="M1.5 4l6.5 5 6.5-5" fill="none" stroke="#fff" stroke-width="1.2"/>
      </svg>
      hvacdalvick@mailbox.com
    </div>
  </div>

  <svg class="ribbon" viewBox="0 0 742 42" preserveAspectRatio="none" aria-hidden="true">
    <polygon points="0,0 392,0 370,42 0,42" fill="var(--brand-blue)"/>
    <polygon points="402,0 742,0 742,42 380,42" fill="var(--brand-red)"/>
  </svg>
  <div class="ribbon__label ribbon__label--family">FAMILY OWNED &amp; OPERATED</div>
  <div class="ribbon__label ribbon__label--licensed">LICENSED &amp; INSURED</div>
</section>

<section class="card card--back">
  <div class="brand-mark"></div>
  <div class="brand-name">DALVICK'S</div>
  <div class="brand-service">AIR CONDITIONING &amp; HEATING SERVICE</div>
  <div class="footer-band"></div>
</section>

</body>
</html>
```